KTWG application splash screen

We need a 1024x768 image for use as an application splash screen.
The image will be displayed full screen on an 10 inch industrial PC 1024x768 screen while our application is launching. The image should convey that the application is "Waiting for connection to Wi-Fi access point..." and include a graphic of the industrial PC connected to the access point via an Ethernet cable. A list of troubleshooting steps should be included at the bottom of the image. The troubleshooting steps should not be the main focus of the image and should be shown in a smaller font (but still readable at 1024x768 displayed on a 10 inch screen).
I will include a mock up of the general idea of what we are looking for as well as image files for the industrial PC, a screenshot of our application to show on the PC's screen and the AP.
For general look and feel and a sense of corporate branding please review our website https://marrowgatesoilworks.example/. The splash screen should reflect corporate branding.
Target Market(s)
Users of our application
Industry/Entity Type
Agriculture
Look and feel

```html
<!DOCTYPE html>
<html lang="en">
<head>
<meta charset="utf-8">
<title>KTWG Splash Screen</title>
<link rel="stylesheet" href="https://fonts.googleapis.com/css2?family=Poppins:wght@400;500;600;700&display=swap">
<style>
  :root {
    --brand-green: #43bd6b;
    --white: #ffffff;
    --stage: #000000;
    --device-dark: #2a2a2a;
    --ap-light: #eef1f0;
  }
  * { box-sizing: border-box; margin: 0; padding: 0; }
  html, body {
    width: 1200px; height: 1200px; overflow: hidden;
    background: var(--stage);
    font-family: "Poppins", sans-serif;
  }
  .canvas { position: relative; width: 1200px; height: 1200px; background: var(--stage); }
  .splash {
    position: absolute; left: 111px; top: 233px;
    width: 979px; height: 734px;
    background: var(--brand-green);
    overflow: hidden;
  }
  .title-card {
    position: absolute; left: 283px; top: 0;
    width: 413px; height: 163px;
    background: var(--white);
    border-radius: 0 0 25px 25px;
    display: flex; align-items: center; justify-content: center;
  }
  .title-card h1 {
    color: var(--brand-green);
    font-weight: 700; font-size: 35px; line-height: 34px;
    letter-spacing: 1.5px; text-align: center;
    margin-top: 8px;
  }
  .device-pc {
    position: absolute; left: 63px; top: 275px;
    width: 219px; height: 174px;
    border-radius: 12px;
    border: 2px solid var(--white);
    background: linear-gradient(180deg, #3a3a3a, var(--device-dark));
  }
  .device-pc .screen {
    position: absolute; left: 19px; top: 17px; width: 177px; height: 130px;
    background: linear-gradient(180deg, #f4f5f5, #dfe6e2);
  }
  .device-ap {
    position: absolute; left: 882px; top: 255px;
    width: 31px; height: 194px;
    border-radius: 6px;
    background: linear-gradient(90deg, #d9dedc, var(--ap-light), #d9dedc);
  }
  .label { position: absolute; color: var(--white); }
  .label .name { font-weight: 600; font-size: 16px; letter-spacing: 1.4px; line-height: 18px; }
  .label .model { font-weight: 400; font-size: 12px; letter-spacing: 1px; line-height: 14px; }
  .label-pc { left: 295px; top: 340px; }
  .label-ap { right: 108px; top: 340px; text-align: right; }
  .cable { position: absolute; left: 295px; top: 378px; }
  .cable-label {
    position: absolute; left: 455px; width: 200px; top: 393px;
    text-align: center; color: var(--white);
    font-weight: 600; font-size: 15px; letter-spacing: 1.4px;
  }
  .help-card {
    position: absolute; left: 276px; top: 579px;
    width: 426px; height: 160px;
    background: var(--white);
    border-radius: 25px 25px 0 0;
    color: var(--brand-green);
  }
  .help-card h2 {
    text-align: center; font-weight: 600; font-size: 14px;
    letter-spacing: 1.2px; margin-top: 11px; line-height: 18px;
  }
  .help-card ul { list-style: none; font-size: 10px; line-height: 11.5px; margin-top: 2px; }
  .help-card li { position: relative; padding-left: 7px; }
  .help-card li::before { content: "•"; position: absolute; left: 0; }
  .help-card > ul { margin-left: 28px; }
  .help-card ul ul { margin-left: 5px; margin-top: 0; }
  .brand-mark {
    position: absolute; left: 855px; top: 615px;
    width: 90px; height: 90px;
    background: var(--stage);
    border: 3px solid var(--white);
    border-radius: 20px;
    display: flex; align-items: center; justify-content: center;
    color: var(--white); font-weight: 700; font-size: 22px; letter-spacing: 1px;
  }
</style>
</head>
<body>
<div class="canvas">
  <main class="splash">
    <header class="title-card">
      <h1>Waiting for connection to Wi-Fi access point...</h1>
    </header>

    <div class="device-pc" role="img" aria-label="Industrial tablet PC showing the KTWG application">
      <div class="screen"></div>
    </div>
    <div class="label label-pc">
      <div class="name">TRACTOR CAB</div>
      <div class="model">COMPUTER</div>
    </div>

    <svg class="cable" width="577" height="6" viewBox="0 0 577 6" aria-hidden="true">
      <line x1="2" y1="3" x2="575" y2="3" stroke="#ffffff" stroke-width="3.4" stroke-linecap="round" stroke-dasharray="0 11.46"/>
    </svg>
    <div class="cable-label">ETHERNET CABLE</div>

    <div class="label label-ap">
      <div class="name">WI-FI ACCESS POINT</div>
      <div class="model">NETARC OAP-220 OUTDOOR</div>
    </div>
    <div class="device-ap" role="img" aria-label="Outdoor Wi-Fi access point with two antennas"></div>

    <section class="help-card">
      <h2>TROUBLESHOOTING STEPS:</h2>
      <ul>
        <li>This screen should only be visible for a short time on boot.</li>
        <li>If this screen stays visible for more than a minute:
          <ul>
            <li>Verify that the Wi-Fi Access Point (AP) powers up when this system does (indicated by a green light on the side of the AP).</li>
            <li>Check the Ethernet cable between this system and the AP for damage, and replace it if necessary.</li>
            <li>Power-cycle this system and wait for it to reboot fully.</li>
            <li>If the issue persists, contact KTWG support for further assistance.</li>
          </ul>
        </li>
      </ul>
    </section>

    <div class="brand-mark">KTWG</div>
  </main>
</div>
</body>
</html>
```